Custom outfit design and creation - where design becomes divine

It is a boutique custom outfit design and creation, we sew for babies to young adults. We offer custom designed, custom made to measure and individually handcrafted outfits for each customer. Head Designer, Miriam Dalby will work with clients to create a one of a kind outfit that is sure to turn heads. Dance and pageant costumes are all made with the best quality fabrics, embellishments and only genuine Velmorra crystals. Thimble Bloom also offers custom embroidery which is done on site with a state of the art embroidery machine and is now offering heat pressed vinyl. We pride ourselves on quality dance and pageant clothing and seek to accommodate a patron's unique style whilst creating winning outfts. I would like a card that incorporates the sewing needle in the title, and also sewing pictures throughout, i want something that is eye-catching. I would also like a Chatterbox logo so people are aware that we are also on ChatterboxI don't care if you don't use the pictures below but that fun type of picture is what i am looking for I do want to use - Where design becomes divine - on the card somewhere
Updates

Project Deadline Extended Reason: I need to see some different types of designs, although if I like something I will go with that straight away Added Monday, February 22, 2016

Industry/Entity Type

Boutique

Contact Information for Business Card

Thimble Bloom Design19 Amberley Drive Pakenham VIC 3810Phone: 0434102697www.sparklestitches.com.au

Requirements
Nice to have
• It doesn't have to be those pictures I posted I just used them as a guide to show that I was after something funky

```html
<!DOCTYPE html>
<html lang="en">
<head>
<meta charset="utf-8">
<title>Thimble Bloom Design – Business Card</title>
<link href="https://fonts.googleapis.com/css2?family=Questrial&family=Montserrat:wght@700&display=swap" rel="stylesheet">
<style>
  :root {
    --backdrop: #1c1c1e;
    --plum: #8e2a8e;
    --plum-light: #b565b5;
    --ink-black: #0b0b0b;
    --paper: #ffffff;
    --muted: #cfcfcf;
  }
  * { margin: 0; padding: 0; box-sizing: border-box; }
  html, body {
    width: 1200px; height: 911px; overflow: hidden;
    background: var(--backdrop);
    font-family: "Questrial", "Century Gothic", sans-serif;
  }
  .canvas { position: relative; width: 1200px; height: 911px; }

  .card {
    position: absolute;
    width: 580px; height: 350px;
    border-radius: 26px;
    overflow: hidden;
  }

  /* ---------- back of card ---------- */
  .card-back {
    left: 560px; top: 70px;
    background: var(--ink-black);
    color: var(--paper);
  }
  .card-back .brand {
    position: absolute; left: 0; right: 0; top: 120px;
    text-align: center;
  }
  .brand-name {
    font-size: 44px; letter-spacing: 1px; line-height: 1;
  }
  .brand-sub {
    display: block; font-size: 20px; letter-spacing: 14px; margin-top: 10px;
    margin-right: -14px;
  }
  .card-back .follow {
    position: absolute; left: 0; right: 0; bottom: 42px;
    display: flex; justify-content: center; align-items: center; gap: 12px;
    font-size: 17px; letter-spacing: 0.5px;
  }
  .follow .social-mark {
    display: inline-flex; align-items: center; gap: 6px;
  }
  .social-mark .dot {
    width: 14px; height: 14px; background: var(--paper); border-radius: 2px;
  }

  /* ---------- front of card ---------- */
  .card-front {
    left: 80px; top: 470px;
    background: var(--paper);
  }
  .card-front .brand {
    position: absolute; left: 60px; top: 42px;
    color: var(--plum);
  }
  .card-front .brand .brand-sub { margin-left: 110px; }
  .wave {
    position: absolute; left: 0; top: 0; width: 580px; height: 350px;
  }
  .contact-list {
    position: absolute; left: 30px; top: 196px;
    list-style: none; color: var(--paper);
    font-size: 17px; line-height: 27px;
  }
  .contact-list li { display: flex; align-items: center; gap: 10px; }
  .contact-list svg { width: 16px; height: 16px; flex: none; }
  .person {
    position: absolute; right: 34px; top: 232px;
    text-align: right; color: var(--paper);
  }
  .person-name {
    font-family: "Montserrat", "Century Gothic", sans-serif;
    font-weight: 700; font-size: 21px;
  }
  .person-role { font-size: 17px; margin-top: 2px; }
  .address {
    position: absolute; right: 34px; bottom: 22px;
    text-align: right; color: var(--paper); font-size: 17px; line-height: 22px;
  }
</style>
</head>
<body>
<main class="canvas">

  <section class="card card-back" aria-label="Card back">
    <div class="brand">
      <span class="brand-name">Thimble Bloom</span>
      <span class="brand-sub">DESIGN</span>
    </div>
    <p class="follow">
      Follow THIMBLE BLOOM
      <span class="social-mark"><span class="dot"></span>Chatterbox</span>
    </p>
  </section>

  <section class="card card-front" aria-label="Card front">
    <svg class="wave" viewBox="0 0 580 350" preserveAspectRatio="none" aria-hidden="true">
      <defs>
        <linearGradient id="plumSheen" x1="0" y1="0" x2="1" y2="0">
          <stop offset="0" stop-color="#8e2a8e"/>
          <stop offset="0.42" stop-color="#8e2a8e"/>
          <stop offset="0.55" stop-color="#b565b5"/>
          <stop offset="0.7" stop-color="#8e2a8e"/>
          <stop offset="1" stop-color="#8e2a8e"/>
        </linearGradient>
      </defs>
      <path d="M0 170 C 140 110, 320 160, 420 205 C 490 235, 550 240, 580 205 L580 350 L0 350 Z" fill="url(#plumSheen)"/>
      <path d="M0 158 C 140 98, 320 150, 420 193 C 490 223, 552 228, 580 195" fill="none" stroke="var(--plum)" stroke-width="3"/>
      <path d="M0 166 C 140 106, 320 158, 420 201 C 490 231, 552 236, 580 201" fill="none" stroke="var(--paper)" stroke-width="3"/>
    </svg>

    <div class="brand">
      <span class="brand-name">Thimble Bloom</span>
      <span class="brand-sub">DESIGN</span>
    </div>

    <ul class="contact-list">
      <li>
        <svg viewBox="0 0 16 16" aria-hidden="true"><path d="M3 2h3l1 3-2 1.5a9 9 0 0 0 4.5 4.5L11 9l3 1v3a1.5 1.5 0 0 1-1.5 1.5A11.5 11.5 0 0 1 1.5 3.5 1.5 1.5 0 0 1 3 2z" fill="#fff"/></svg>
        0471 958 364
      </li>
      <li>
        <svg viewBox="0 0 16 16" aria-hidden="true"><rect x="1" y="3.5" width="14" height="9" fill="none" stroke="#fff" stroke-width="1.5"/><path d="M1 3.5l7 5.5 7-5.5" fill="none" stroke="#fff" stroke-width="1.5"/></svg>
        design@thimblebloomx.com.au
      </li>
      <li>
        <svg viewBox="0 0 16 16" aria-hidden="true"><circle cx="8" cy="8" r="6.5" fill="none" stroke="#fff" stroke-width="1.3"/><ellipse cx="8" cy="8" rx="3" ry="6.5" fill="none" stroke="#fff" stroke-width="1.1"/><path d="M1.5 8h13M3 4.5h10M3 11.5h10" stroke="#fff" stroke-width="1.1"/></svg>
        www.thimblebloomx.com.au
      </li>
    </ul>

    <div class="person">
      <p class="person-name">Miriam Dalby</p>
      <p class="person-role">Head Designer</p>
    </div>
    <p class="address">47 Wendover Lane<br>Larchfield VIC 3927</p>
  </section>

</main>
</body>
</html>
```